Casino with the 'highest winning percentage' needs a stationery design

This is for a casino in Colombo, Sri Lanka and we need a stationery design for business card, letter head and envelope.

Should be very professional, simple and elegant without fancy fonts

Reason: Not fully satisfied with the designs. Need more designs.

Business

• 1. card deck symbol 'CLUBS' in red, or black

2. name in BLOCK CAPITAL LETTERS

3. Preferred font colours are black, white or red

4. Prefer 'professional /elegant' fonts
• SHOULD NOT HAVE ANY OTHER SYMBOL EXCEPT 'CLUBS'

DO NOT PREFER ITALIC FONTS

```html
<!DOCTYPE html>
<html lang="en">
<head>
<meta charset="utf-8">
<title>Marlowe Entertainment – Letterhead</title>
<link rel="stylesheet" href="https://fonts.googleapis.com/css2?family=Questrial&display=swap">
<style>
  :root {
    --backdrop: #dcdcdc;
    --paper: #ffffff;
    --ink: #2b2b2b;
    --ink-soft: #555555;
    --rule: #8a8a8a;
  }
  * { box-sizing: border-box; margin: 0; padding: 0; }
  html, body {
    width: 1200px;
    height: 799px;
    overflow: hidden;
    background: var(--backdrop);
  }
  .letterhead {
    position: absolute;
    left: 338px;
    top: 29px;
    width: 524px;
    height: 741px;
    background: var(--paper);
    box-shadow: 0 2px 10px rgba(0, 0, 0, 0.12);
  }
  .brand {
    position: absolute;
    left: 42px;
    top: 62px;
    display: flex;
    align-items: center;
    gap: 8px;
  }
  .brand-square {
    width: 9px;
    height: 9px;
    background: var(--ink);
  }
  .brand-name {
    font-family: "Questrial", "Century Gothic", sans-serif;
    font-weight: 400;
    font-size: 13px;
    letter-spacing: 2.4px;
    color: var(--ink);
    text-transform: uppercase;
    line-height: 1;
    white-space: nowrap;
  }
  .contact-bar {
    position: absolute;
    left: 0;
    right: 0;
    bottom: 30px;
    height: 26px;
  }
  .contact-item {
    position: absolute;
    top: 0;
    height: 26px;
    padding-left: 7px;
    padding-top: 1px;
    border-left: 1px solid var(--rule);
    font-family: "Questrial", "Century Gothic", sans-serif;
    font-style: normal;
    font-size: 7.5px;
    line-height: 10px;
    color: var(--ink-soft);
    display: flex;
    flex-direction: column;
    white-space: nowrap;
  }
  .contact-item strong { color: var(--ink); font-weight: 700; }
  .contact-address { left: 96px; }
  .contact-phone { left: 270px; }
  .contact-web { left: 404px; }
</style>
</head>
<body>
  <main class="letterhead">
    <header class="brand">
      <span class="brand-square" aria-hidden="true"></span>
      <h1 class="brand-name">Marlowe Entertainment</h1>
    </header>
    <footer class="contact-bar">
      <address class="contact-item contact-address">
        <span>52, Harbour View Road</span>
        <span>Colombo 01000, Sri Lanka</span>
      </address>
      <div class="contact-item contact-phone">
        <span><strong>Tel:</strong> + 94 11 2045870</span>
        <span><strong>Fax:</strong> + 94 11 2045871</span>
      </div>
      <div class="contact-item contact-web">
        <span>www.<strong>marlowecolombo</strong>.com</span>
      </div>
    </footer>
  </main>
</body>
</html>
```